The Lantern Guild Pitchdeck Template

The Lantern Guild would like a branded pitch deck template design for members to use when presenting their projects and proposals. The deck should include 10-15 different slide designs, each with the same branded theme, but with a variety of icon graphics and other design features that will empower members to easily create a beautiful pitch deck just by adding written content.

Please visit lanternguildhq.org to get a sense for our branding - purple, space, galaxy, white font and the planetary logo are some commonalities.

Here are 2 google drive links with some additional designs

https://files.boxmeadow.net/share/f/8QzrTa2Lk5VbNw7cHyP0dJe3sUmXg4RiF

https://files.boxmeadow.net/share/f/3Kd9-Rm6Tq2-yLvBn051fopwxhcT_zj7

```html
<!DOCTYPE html>
<html lang="en">
<head>
<meta charset="utf-8">
<title>The Lantern Guild Pitch Deck Template</title>
<link rel="stylesheet" href="https://fonts.googleapis.com/css2?family=Montserrat:wght@400;500;600;700&family=Arimo:wght@400;700&display=swap">
<style>
  :root {
    --canvas: #f3f4f8;
    --white: #ffffff;
    --deep-violet: #48119f;
    --bright-violet: #6a10d8;
    --ink-violet: #3d0e99;
    --night-violet: #231056;
    --edge-violet: #5b22cf;
    --shadow: rgba(20, 10, 60, 0.18);
  }
  * { margin: 0; padding: 0; box-sizing: border-box; }
  html, body { width: 1200px; height: 4208px; overflow: hidden; }
  body {
    background: var(--canvas);
    font-family: "Arimo", Arial, sans-serif;
    color: var(--white);
    position: relative;
  }
  .slide {
    position: absolute;
    left: 51px;
    width: 1098px;
    height: 618px;
    overflow: hidden;
    box-shadow: 0 2px 6px var(--shadow);
  }
  .slide--cover { top: 70px; background: #0b1a33; }
  .slide--about { top: 751px; background: var(--deep-violet); }
  .slide--vision { top: 1433px; background: var(--bright-violet); }
  .slide--intentions { top: 2116px; background: var(--ink-violet); }
  .slide--partners { top: 2798px; background: var(--ink-violet); }
  .slide--thanks { top: 3509px; background: var(--night-violet); }

  /* cover */
  .cover-art {
    position: absolute; inset: 0;
    background:
      radial-gradient(ellipse 30% 40% at 52% 48%, #cfe9f0 0%, #5fa6bf 25%, transparent 60%),
      radial-gradient(ellipse 70% 60% at 50% 35%, #1f5f82 0%, #123b5c 45%, #0a1a33 80%),
      linear-gradient(#0a1a33, #201a2a);
  }
  .cover-ground {
    position: absolute; left: 0; right: 0; bottom: 0; height: 150px;
    background: linear-gradient(transparent, #2a1f28 60%, #1a1218);
  }
  .cover-brand {
    position: absolute; left: 0; right: 0; top: 232px;
    text-align: center;
    font-family: "Montserrat", sans-serif;
    font-weight: 600; font-size: 96px; letter-spacing: 34px;
    padding-left: 34px; line-height: 1;
  }
  .cover-tagline {
    position: absolute; left: 0; right: 0; top: 343px;
    text-align: center;
    font-family: "Montserrat", sans-serif;
    font-weight: 500; font-size: 25px; letter-spacing: 10px;
    padding-left: 10px;
  }

  /* shared slide parts */
  .slide-heading {
    position: absolute; left: 33px; top: 41px;
    padding-left: 19px; height: 62px;
    border-left: 2px solid var(--white);
  }
  .slide-title {
    font-family: "Montserrat", sans-serif;
    font-weight: 700; font-size: 26px; line-height: 1; margin-top: 8px;
  }
  .slide-subtitle {
    font-family: "Montserrat", sans-serif;
    font-weight: 400; font-size: 12px; margin-top: 7px; letter-spacing: 0.3px;
  }
  .slide-footer {
    position: absolute; left: 26px; right: 20px; bottom: 20px;
    display: flex; justify-content: space-between;
    font-size: 12px;
  }
  .corner-mark {
    position: absolute; right: 20px; top: 40px;
    display: flex; align-items: center; gap: 7px;
    font-family: "Montserrat", sans-serif; font-weight: 700; font-size: 15px;
    letter-spacing: 2px;
  }
  .corner-mark::before {
    content: ""; width: 14px; height: 14px; border-radius: 50%;
    border: 2px solid var(--white);
  }
  .body-copy {
    position: absolute; z-index: 1; font-size: 13px; line-height: 23px; text-align: justify;
  }
  .body-copy p + p { margin-top: 23px; }

  /* about */
  .about-copy { left: 34px; top: 155px; width: 435px; }
  .about-art {
    position: absolute; left: 515px; top: 120px; width: 560px; height: 380px;
    border-radius: 50%;
    background: radial-gradient(ellipse at 50% 45%, #e9ddff 0%, #9a8ae6 30%, #3d49b8 60%, rgba(72,17,159,0) 72%);
  }

  /* vision */
  .vision-item {
    position: absolute; top: 134px; width: 320px; margin-left: -160px;
    text-align: center;
  }
  .vision-item:nth-of-type(1) { left: 185px; }
  .vision-item:nth-of-type(2) { left: 542px; }
  .vision-item:nth-of-type(3) { left: 900px; }
  .vision-art {
    width: 209px; height: 209px; border-radius: 50%; margin: 0 auto;
  }
  .vision-art--people { background: linear-gradient(160deg, #8d78c9 0%, #5f4b8f 45%, #39602f 100%); }
  .vision-art--planet { background: radial-gradient(circle at 45% 40%, #d7e6c6 0%, #6fa6c8 40%, #2d5f9a 75%, #3c4f8f 100%); }
  .vision-art--peace { background: linear-gradient(180deg, #fbd9a8 0%, #f59a3b 50%, #b7401a 80%, #6a1e2a 100%); }
  .vision-title {
    font-family: "Montserrat", sans-serif; font-weight: 600; font-size: 25px;
    margin-top: 24px; letter-spacing: 0.5px;
  }
  .vision-text { font-size: 13px; line-height: 23px; margin-top: 11px; }

  /* intentions */
  .intentions-copy { left: 36px; top: 163px; width: 441px; line-height: 22.4px; }
  .intentions-art { position: absolute; inset: 0; }

  /* partners */
  .partner {
    position: absolute; top: 152px; width: 248px; text-align: center;
  }
  .partner:nth-of-type(1) { left: 16px; }
  .partner:nth-of-type(2) { left: 289px; }
  .partner:nth-of-type(3) { left: 562px; }
  .partner:nth-of-type(4) { left: 834px; }
  .partner-art {
    height: 196px; border: 1.5px solid #c9c2e6; border-radius: 3px;
  }
  .partner-art--collective { background: radial-gradient(ellipse at 50% 50%, #6a4fb8 0%, #2c1a5e 60%, #150c33 100%); }
  .partner-art--kernel { background: radial-gradient(circle at 50% 50%, #2d8a3e 0%, #1d2a22 45%, #1b1b1b 70%); }
  .partner-art--kindred { background: radial-gradient(circle at 50% 50%, #6b5527 0%, #1d1a15 55%, #121212 80%); }
  .partner-art--brightwave { background: radial-gradient(circle at 50% 50%, #3aa6d8 0%, #2a5d9a 40%, #16182a 75%); }
  .partner-name {
    font-family: "Montserrat", sans-serif; font-weight: 600; font-size: 13px;
    margin-top: 26px; text-transform: uppercase;
  }
  .partner-text { font-size: 9px; line-height: 15.5px; margin-top: 14px; padding: 0 10px; }

  /* thanks */
  .thanks-glow {
    position: absolute; inset: 0;
    background: radial-gradient(ellipse 80% 60% at 50% 100%, #3a2378 0%, transparent 70%);
  }
  .thanks-brand {
    position: absolute; left: 0; right: 0; top: 150px;
    display: flex; justify-content: center; align-items: center; gap: 22px;
    font-family: "Montserrat", sans-serif; font-weight: 700; font-size: 56px;
    letter-spacing: 6px; line-height: 1;
  }
  .thanks-brand::before {
    content: ""; width: 96px; height: 96px; border-radius: 50%;
    border: 12px solid var(--white);
  }
  .thanks-title {
    position: absolute; left: 0; right: 0; top: 365px;
    text-align: center;
    font-family: "Montserrat", sans-serif; font-weight: 700; font-size: 98px;
    line-height: 1;
  }
</style>
</head>
<body>

<section class="slide slide--cover">
  <div class="cover-art" role="img" aria-label="Photograph of a glowing galaxy over a desert landscape with a lone figure"></div>
  <div class="cover-ground"></div>
  <h1 class="cover-brand">LUMEN</h1>
  <p class="cover-tagline">LANTERN COLLECTIVE</p>
</section>

<section class="slide slide--about">
  <div class="about-art" role="img" aria-label="Galaxy-filled planet illustration with a figure standing on its surface"></div>
  <header class="slide-heading">
    <h2 class="slide-title">ABOUT US</h2>
    <p class="slide-subtitle">SUBTITLE GOES HERE</p>
  </header>
  <div class="body-copy about-copy">
    <p>The Lantern Guild is a spiritual, conscious and regenerative non-profit organisation established for furthering the upliftment, enlightenment, spiritual realisation, and general welfare of people throughout the world, the betterment of life on planet Earth, and other spiritual, environmental, humanitarian, and beneficent purpose.</p>
    <p>Buddhism, Christianity, Hinduism, Islam, Judaism and other religions are belief systems; The Universe exists whether you believe in it or not.</p>
    <p>The Lantern Guild is a spiritual, conscious and regenerative non-profit organisation established for furthering the upliftment, enlightenment, spiritual realisation, and general welfare of people throughout the world, the betterment of life on planet Earth, and other spiritual, environmental, humanitarian, and beneficent purpose.</p>
  </div>
  <footer class="slide-footer"><span>© Copyright 2022 The Lantern Guild.All Rights Reserved.</span><span>Page 01</span></footer>
</section>

<section class="slide slide--vision">
  <header class="slide-heading">
    <h2 class="slide-title">WHAT WE ENVISION</h2>
    <p class="slide-subtitle">SUBTITLE GOES HERE</p>
  </header>
  <div class="corner-mark">LUMEN</div>
  <article class="vision-item">
    <div class="vision-art vision-art--people" role="img" aria-label="Photograph of two children in a lavender field"></div>
    <h3 class="vision-title">PEOPLE</h3>
    <p class="vision-text">A World that meets the needs of every<br>human being as a birth right, providing the<br>foundation for self-actualisation.</p>
  </article>
  <article class="vision-item">
    <div class="vision-art vision-art--planet" role="img" aria-label="Watercolour illustration of planet Earth"></div>
    <h3 class="vision-title">PLANET</h3>
    <p class="vision-text">A World that lives in harmony with Nature;<br>restore and protect Mother Earth, including<br>the Animal Kingdom</p>
  </article>
  <article class="vision-item">
    <div class="vision-art vision-art--peace" role="img" aria-label="Photograph of a bird in flight against a sunset"></div>
    <h3 class="vision-title">PEACE</h3>
    <p class="vision-text">A World that chooses peace, love and<br>harmony, awake and aware of its connection<br>with everything.</p>
  </article>
  <footer class="slide-footer"><span>© Copyright 2022 The Lantern Guild.All Rights Reserved.</span><span>Page 02</span></footer>
</section>

<section class="slide slide--intentions">
  <svg class="intentions-art" width="1098" height="618" viewBox="0 0 1098 618" role="img" aria-label="Surreal landscape of a ringed planet system above a red sunset shore with a lone figure">
    <defs>
      <linearGradient id="sunset-scene" x1="0" y1="0" x2="0" y2="1">
        <stop offset="0" stop-color="#3a2436"/>
        <stop offset="0.3" stop-color="#b44a4a"/>
        <stop offset="0.5" stop-color="#6e3550"/>
        <stop offset="0.75" stop-color="#8a3a4e"/>
        <stop offset="1" stop-color="#2b1a26"/>
      </linearGradient>
    </defs>
    <path d="M631,0 Q445,309 631,618 L1098,618 L1098,0 Z" fill="#5b22cf"/>
    <path d="M643,0 Q457,309 643,618 L1098,618 L1098,0 Z" fill="url(#sunset-scene)"/>
  </svg>
  <header class="slide-heading">
    <h2 class="slide-title">INTENTIONS</h2>
    <p class="slide-subtitle">SUBTITLE GOES HERE</p>
  </header>
  <div class="corner-mark">LUMEN</div>
  <div class="body-copy intentions-copy">
    <p>The Lantern Guild, members, missionaries, stewards sponsors, partners, and donors are working on various initiatives to fulfil our intentions. As a collective are focusing on every area; from education, healthcare, economics, finance, governance &amp; technology, to space travel, art, music and transformational experiences. Our mission is to protect the Spirit of Air, Water, Land and Food; to create a system that supports the people and the planet; to redistribute wealth; protect human rights; serve justice and implement the conscious economy. We are focused on building a global community, transforming local environments, integration with Indigenous tribes and the reformation of society. We are interested in new paradigm schools and Universities, incubators for regenerative technology, natural medicine, empowering micro-industries, entrepreneurs, investors, inventors, artists and creatives. If you are involved in any initiative that benefits the collective, we would love to support you.</p>
  </div>
  <footer class="slide-footer"><span>© Copyright 2022 The Lantern Guild.All Rights Reserved.</span><span>Page 03</span></footer>
</section>

<section class="slide slide--partners">
  <header class="slide-heading">
    <h2 class="slide-title">PARTNERS</h2>
    <p class="slide-subtitle">SUBTITLE GOES HERE</p>
  </header>
  <div class="corner-mark">LUMEN</div>
  <article class="partner">
    <div class="partner-art partner-art--collective" role="img" aria-label="Nebula artwork for the Lantern Collective partner"></div>
    <h3 class="partner-name">Lantern Collective</h3>
    <p class="partner-text">A group of conscious organisations working together across the collective, setting shared standards for what it means to be conscious, regenerative and fair for people, the planet and a conscious economy.</p>
  </article>
  <article class="partner">
    <div class="partner-art partner-art--kernel" role="img" aria-label="Partner badge for Kernel Pay"></div>
    <h3 class="partner-name">Kernel Pay</h3>
    <p class="partner-text">Regenerative Money<br>A payment platform and financial ecosystem that helps people and communities heal the planet. Built from systems that reflect new thinking in finance, social and political innovation, it connects regenerative culture.</p>
  </article>
  <article class="partner">
    <div class="partner-art partner-art--kindred" role="img" aria-label="Partner badge for Kindred Circle"></div>
    <h3 class="partner-name">Kindred Circle</h3>
    <p class="partner-text">Rainbow Entrepreneurs<br>A high level network of game changers who are not only leading in their own field, but who are also dedicated to extending human life on Earth for as long as possible.</p>
  </article>
  <article class="partner">
    <div class="partner-art partner-art--brightwave" role="img" aria-label="Partner badge for Brightwave Commons"></div>
    <h3 class="partner-name">Brightwave Commons</h3>
    <p class="partner-text">An ecosystem for personal growth<br>An immersive experiential network of yoga, meditation, mindfulness, virtual reality, online learning, digital music, personal development, wellness and more.</p>
  </article>
  <footer class="slide-footer"><span>© Copyright 2022 The Lantern Guild.All Rights Reserved.</span><span>Page 04</span></footer>
</section>

<section class="slide slide--thanks">
  <div class="thanks-glow"></div>
  <div class="thanks-brand">LUMEN</div>
  <h2 class="thanks-title">THANK YOU</h2>
</section>

</body>
</html>
```